BUSINESS CARD - HALLORAN FIELD SERVICES

I would like to create a business card for my fertilizer spreading business. I would like to incorporate my existing logo and also a description of the services offered. The business card will be given to farmers so must be kept simple but effective. It will also be left in stores so much also be eye catching in order to stand out from other cards.

Target Market(s)

FARMERS

Requirements
Must have
• FRONT OF CARD = EXISTING LOGO + "CUSTOMISED SPREADING" below the logo

REAR Of CARD = SERVICES OFFERED AND CONTACT DETAILS

- Bulk fertilizer including Lime, Gypsum, Manure & Compost
- Granular fertilizer including Single Super, Urea, Gran-am, & Custom Blends
- Modern equipment - Autosteer & Variable Rate Capable
- Friendly & Reliable Service
- Contact Gus: 0417 552 308
Nice to have
• utilize same color scheme as existing logo

```html
<!DOCTYPE html>
<html lang="en">
<head>
<meta charset="utf-8">
<title>Halloran Field Services – Business Card</title>
<link rel="stylesheet" href="https://fonts.googleapis.com/css2?family=Montserrat:wght@400;500;700&display=swap">
<style>
  :root {
    --bg: #8a8a8c;
    --card-light: #ffffff;
    --card-dark: #3b3b3d;
    --ink: #3a3a3c;
    --ink-soft: #5a5a5c;
    --orange: #f28a1a;
    --text-on-dark: #e6e6e6;
  }
  * { box-sizing: border-box; margin: 0; padding: 0; }
  html, body { width: 1200px; height: 800px; overflow: hidden; }
  body {
    background: var(--bg);
    font-family: "Montserrat", sans-serif;
    display: flex;
    align-items: center;
    justify-content: center;
    gap: 40px;
  }
  .card {
    width: 540px;
    height: 310px;
    position: relative;
    border-bottom: 4px solid var(--orange);
    box-shadow: 0 14px 30px rgba(0,0,0,0.25);
  }

  /* Contact side */
  .card--front {
    background: var(--card-light);
    display: flex;
    align-items: center;
    padding: 0 36px;
  }
  .brand {
    width: 230px;
    display: flex;
    flex-direction: column;
    align-items: flex-start;
    gap: 8px;
  }
  .brand__row { display: flex; align-items: center; gap: 10px; }
  .brand__mark { width: 40px; height: 40px; flex: none; }
  .brand__name {
    font-weight: 700;
    font-size: 17px;
    line-height: 1.15;
    color: var(--ink);
    letter-spacing: -0.2px;
  }
  .brand__tagline {
    font-size: 10px;
    letter-spacing: 1.6px;
    color: var(--ink-soft);
    border-top: 1.5px solid var(--orange);
    padding-top: 5px;
    margin-left: 50px;
  }
  .divider {
    width: 1px;
    height: 110px;
    background: var(--ink-soft);
    margin: 0 26px;
  }
  .contact { display: flex; flex-direction: column; }
  .contact__name {
    font-weight: 700;
    font-size: 17px;
    color: var(--ink);
    letter-spacing: 0.5px;
  }
  .contact__role {
    font-size: 12px;
    color: var(--orange);
    margin-bottom: 12px;
  }
  .contact__list { list-style: none; display: flex; flex-direction: column; gap: 5px; }
  .contact__item {
    display: flex; align-items: center; gap: 8px;
    font-size: 11px; color: var(--ink);
  }
  .contact__icon { width: 11px; height: 11px; flex: none; fill: var(--ink); }

  /* Services side */
  .card--back {
    background: var(--card-dark);
    display: flex;
    flex-direction: column;
    align-items: center;
    justify-content: center;
    gap: 22px;
  }
  .emblem {
    width: 130px;
    height: 130px;
    border-radius: 50%;
    background: radial-gradient(circle at 40% 35%, #5a5a5c, #2a2a2c);
  }
  .services {
    list-style: none;
    text-align: center;
    color: var(--text-on-dark);
    font-size: 11.5px;
    line-height: 1.55;
  }
</style>
</head>
<body>

  <section class="card card--front" aria-label="Business card contact side">
    <div class="brand">
      <div class="brand__row">
        <svg class="brand__mark" viewBox="0 0 40 40" aria-hidden="true">
          <circle cx="20" cy="20" r="17" fill="none" stroke="var(--ink)" stroke-width="4"/>
        </svg>
        <span class="brand__name">Halloran Field Services</span>
      </div>
      <span class="brand__tagline">CUSTOMISED SPREADING</span>
    </div>

    <div class="divider"></div>

    <div class="contact">
      <span class="contact__name">GUS HALLORAN</span>
      <span class="contact__role">President</span>
      <ul class="contact__list">
        <li class="contact__item">
          <svg class="contact__icon" viewBox="0 0 24 24" aria-hidden="true"><path d="M6.6 10.8a15.1 15.1 0 0 0 6.6 6.6l2.2-2.2c.3-.3.7-.4 1-.2 1.1.4 2.3.6 3.6.6.6 0 1 .4 1 1V20c0 .6-.4 1-1 1A17 17 0 0 1 3 4c0-.6.4-1 1-1h3.5c.6 0 1 .4 1 1 0 1.3.2 2.5.6 3.6.1.3 0 .7-.2 1z"/></svg>
          0417 552 308
        </li>
        <li class="contact__item">
          <svg class="contact__icon" viewBox="0 0 24 24" aria-hidden="true"><path d="M2 5h20v14H2zm2 2v.5l8 5 8-5V7z"/></svg>
          info@halloranfield.com
        </li>
        <li class="contact__item">
          <svg class="contact__icon" viewBox="0 0 24 24" aria-hidden="true"><circle cx="12" cy="12" r="10"/></svg>
          www.halloranfield.com
        </li>
      </ul>
    </div>
  </section>

  <section class="card card--back" aria-label="Business card services side">
    <div class="emblem" role="img" aria-label="Embossed emblem area with livestock and leaf artwork"></div>
    <ul class="services">
      <li>Bulk fertilizer including Lime, Gypsum, Manure &amp; Compost</li>
      <li>Granular fertilizer including Single Super, Urea, Gran-am, &amp; Custom Blends</li>
      <li>Modern equipment - Autosteer &amp; Variable Rate Capable</li>
      <li>Friendly &amp; Reliable Service</li>
    </ul>
  </section>

</body>
</html>
```